Coastline Premier Retreats Business Card Design

Design a business card for Coastline Premier Retreats. Look at the website for colors and reference. Card should have logo, name, title, office number, mobile number, email, URL and a tagline like, "Luxury Hotel & Resort Email Marketing" (This might change).

https://www.coastlinepremierretreats.example

The rest I will leave up to your imagination.

Contact Information for Business Card

Logo, name, title, office number, mobile number, email, URL and a tagline like, "Luxury Hotel & Resort Email Marketing" (This might change).

```html
<!DOCTYPE html>
<html lang="en">
<head>
<meta charset="utf-8">
<title>Coastline Premier Retreats — Business Card</title>
<link rel="stylesheet" href="https://fonts.googleapis.com/css2?family=Open+Sans:wght@400;600;700;800&display=swap">
<style>
  :root {
    --bg: #222222;
    --card: #fffef3;
    --accent: #f47a20;
    --ink: #111111;
    --card-w: 340px;
    --card-h: 600px;
    --curve: 160px;
  }
  * { box-sizing: border-box; margin: 0; padding: 0; }
  html, body {
    width: 1200px; height: 780px; overflow: hidden;
    background: var(--bg);
    font-family: "Open Sans", Arial, sans-serif;
  }
  .stage {
    width: 1200px; height: 780px;
    display: flex; align-items: center; justify-content: center; gap: 90px;
  }
  .card {
    position: relative;
    width: var(--card-w); height: var(--card-h);
    background: var(--card);
    border: 2px solid var(--accent);
    overflow: hidden;
  }
  /* back side */
  .card--back { border-radius: var(--curve) 0 var(--curve) 0; }
  .back-wordmark {
    position: absolute; left: 50%; top: 50%;
    transform: translate(-50%, -50%) rotate(-90deg);
    white-space: nowrap; text-align: center;
    color: var(--ink);
  }
  .back-wordmark .brand {
    font-weight: 800; font-size: 40px; letter-spacing: 3px; text-transform: uppercase;
    line-height: 1.15;
  }
  .back-rule {
    position: absolute; left: 72px; top: 95px; bottom: 95px; width: 5px;
    background: var(--accent);
  }
  /* front side */
  .card--front { border-radius: 0 var(--curve) 0 var(--curve); }
  .front-logo {
    position: absolute; left: 34px; top: 58px;
    font-weight: 800; font-size: 19px; letter-spacing: 1.5px; text-transform: uppercase;
    color: var(--ink); line-height: 1.2;
  }
  .identity { position: absolute; left: 34px; top: 300px; right: 20px; }
  .person-name { font-weight: 800; font-size: 30px; line-height: 1.1; color: var(--ink); }
  .person-name .first { color: var(--accent); }
  .person-title { font-size: 14px; font-weight: 600; color: var(--ink); margin-top: 4px; }
  .tagline { margin-top: 18px; font-size: 14px; color: var(--accent); line-height: 1.35; }
  .contacts { list-style: none; margin-top: 16px; }
  .contacts li {
    display: flex; align-items: center; gap: 8px;
    font-size: 12.5px; color: var(--ink); line-height: 1.9; white-space: nowrap;
  }
  .contacts svg { width: 13px; height: 13px; flex: none; fill: none; stroke: var(--accent); stroke-width: 2; }
</style>
</head>
<body>
<main class="stage">
  <section class="card card--back" aria-label="Card back">
    <div class="back-rule"></div>
    <div class="back-wordmark">
      <div class="brand">Coastline Premier</div>
      <div class="brand">Retreats</div>
    </div>
  </section>

  <section class="card card--front" aria-label="Card front">
    <div class="front-logo">Coastline Premier<br>Retreats</div>
    <div class="identity">
      <h1 class="person-name"><span class="first">Marisa</span> Delvane</h1>
      <p class="person-title">Co-Founder</p>
      <p class="tagline">Luxury Hotel &amp;<br>Resort Email Marketing</p>
      <ul class="contacts">
        <li><svg viewBox="0 0 24 24"><path d="M5 3h4l2 5-3 2a11 11 0 0 0 6 6l2-3 5 2v4a2 2 0 0 1-2 2A17 17 0 0 1 3 5a2 2 0 0 1 2-2z"/></svg>(555) 014-2758</li>
        <li><svg viewBox="0 0 24 24"><rect x="7" y="2" width="10" height="20" rx="2"/><path d="M11 18h2"/></svg>(555) 014-7777</li>
        <li><svg viewBox="0 0 24 24"><circle cx="12" cy="12" r="9"/><path d="M3 12h18M12 3c3 3 3 15 0 18M12 3c-3 3-3 15 0 18"/></svg>www.coastlinepremierretreats.example</li>
        <li><svg viewBox="0 0 24 24"><rect x="3" y="5" width="18" height="14" rx="1"/><path d="M3 6l9 7 9-7"/></svg>info@coastlinepremierretreats.example</li>
      </ul>
    </div>
  </section>
</main>
</body>
</html>
```